Diverse, up-scale salon needs eye-catching, unique business cards.

We are looking for a unique business card design for our stylist but that can also be multi functional and used for appointment reminder and referrals. I will need a design in a format that I can modify names and titles going forward. In the past we have had a dark background with the logo on one side, and stylist and contact information on the other but we are open to all ideas. I have included our mission statement as well as branded colors below. The statement doesn't need to go on the card, it's just a reference for target market. We need space for the stylists name, title, instagram handle and then the salons phone number, website and address. I am also open to adding a spot for a qr code linked to the stylist instagram or the salon booking link.

primary brand colors:
#333333 #233415 #36502a #93874a #000000
Mission statement:
Vessolin Hair Studio, a high-end salon located in the lively Downtown Farmington, Michigan, is committed to providing exceptional services in a welcoming and relaxed environment to meet the needs of our diverse clientele.
Our salon specializes in contemporary custom haircuts, coloring, extensions, and barbering and beard grooming services. Our team of skilled stylists is passionate and inventive in their hair styling techniques. At the heart of our salon are values centered on quality, innovation, creativity, and above all, comfort. These core values are evident in every appointment across our customizable array of services.
Our goal is to establish a benchmark for exceptional hair care for every human.
Website: www.vessolinhairstudio.example
instagram: @vessolinhairstudio
address: 41782 Pelham Crest Rd, Farmington MI
phone: 248-613-4087

Industry/Entity Type

Hair Salon

Contact Information for Business Card

Stylist name, title, phone, instagram, website, address, (optional qr code)

Requirements
Should not have
• Does not need mission statement on the card.

```html
<!DOCTYPE html>
<html lang="en">
<head>
<meta charset="utf-8">
<title>Vessolin Hair Studio – Business Card</title>
<link href="https://fonts.googleapis.com/css2?family=Arimo:wght@400;700&display=swap" rel="stylesheet">
<style>
  :root {
    --gold: #93874a;
    --charcoal: #333333;
    --backdrop: #1b1b1b;
    --white: #ffffff;
    --rule: #d9d9d9;
    --crescent: #8a8783;
  }
  * { margin: 0; padding: 0; box-sizing: border-box; }
  html, body { width: 1200px; height: 1059px; overflow: hidden; }
  body {
    position: relative;
    background: var(--backdrop);
    font-family: "Arimo", Arial, sans-serif;
    color: var(--white);
  }
  .card { position: absolute; overflow: hidden; }

  /* Front */
  .card-front { left: 258px; top: 89px; width: 689px; height: 393px; background: var(--gold); }
  .card-front .front-shape { position: absolute; inset: 0; }
  .stylist { position: absolute; left: 35px; top: 58px; }
  .stylist-name { font-weight: 700; font-size: 18.5px; line-height: 18px; letter-spacing: 0.1px; }
  .stylist-title { font-size: 17px; line-height: 18px; }
  .address { position: absolute; left: 35px; top: 152px; font-size: 17.5px; line-height: 24px; }
  .contacts { position: absolute; left: 35px; top: 256px; list-style: none; }
  .contacts li { display: flex; align-items: center; height: 28.5px; font-size: 18.5px; }
  .contacts svg { width: 16px; height: 16px; margin-right: 9px; flex: none; }
  .front-brand {
    position: absolute; left: 423px; top: 106px; width: 180px; height: 180px;
    border: 3px solid var(--gold); border-radius: 50%;
    display: flex; align-items: center; justify-content: center; text-align: center;
    color: var(--gold); font-weight: 700; font-size: 22px; line-height: 26px;
    letter-spacing: 1px; text-transform: uppercase;
  }

  /* Back */
  .card-back { left: 252px; top: 540px; width: 701px; height: 401px; background: var(--charcoal); }
  .back-brand {
    position: absolute; left: 237px; top: 69px; width: 216px; height: 216px;
    border: 3px solid var(--gold); border-radius: 50%;
    display: flex; align-items: center; justify-content: center; text-align: center;
    color: var(--gold); font-weight: 700; font-size: 26px; line-height: 31px;
    letter-spacing: 1.2px; text-transform: uppercase;
  }
  .services-heading { position: absolute; left: 48px; top: 320px; width: 604px; height: 26px; }
  .services-heading::before, .services-heading::after {
    content: ""; position: absolute; top: 12px; height: 1.5px; background: var(--rule);
  }
  .services-heading::before { left: 0; width: 213px; }
  .services-heading::after { right: 0; width: 214px; }
  .services-pill {
    position: absolute; left: 222px; top: 0; width: 163px; height: 25px;
    background: var(--gold); border-radius: 13px;
    color: var(--charcoal); font-weight: 700; font-size: 18.5px; line-height: 25px; text-align: center;
  }
  .services-list {
    position: absolute; left: 46px; top: 352px; width: 612px;
    display: flex; justify-content: space-between; list-style: none;
    font-size: 17.5px; white-space: nowrap;
  }
  .services-list li::before {
    content: ""; display: inline-block; width: 7px; height: 7px; border-radius: 50%;
    background: var(--white); margin-right: 4px; vertical-align: 3px;
  }
</style>
</head>
<body>
  <section class="card card-front" aria-label="Business card front">
    <svg class="front-shape" viewBox="0 0 689 393" aria-hidden="true">
      <path d="M422 0 A 214 214 0 0 0 422 393 L689 393 L689 0 Z" fill="var(--white)"/>
      <path d="M428 0 A 214 214 0 0 0 428 393 L689 393 L689 0 Z" fill="var(--crescent)"/>
      <path d="M442 0 A 222 222 0 0 0 442 393 L689 393 L689 0 Z" fill="var(--white)"/>
    </svg>

    <div class="stylist">
      <p class="stylist-name">MARCUS DELANO</p>
      <p class="stylist-title">Manager</p>
    </div>

    <p class="address">41782 Pelham Crest Rd<br>Farmington MI</p>

    <ul class="contacts">
      <li>
        <svg viewBox="0 0 16 16" aria-hidden="true"><path d="M4 1.5 L6 4.5 L4.8 6 C5.6 7.8 7.6 9.8 9.6 10.8 L11 9.6 L14 11.6 L12.6 14 C7 13.6 2.2 8.6 1.8 3 Z" fill="none" stroke="var(--white)" stroke-width="1.5" stroke-linejoin="round"/></svg>
        248-613-4087
      </li>
      <li>
        <svg viewBox="0 0 16 16" aria-hidden="true"><circle cx="8" cy="8" r="6.5" fill="none" stroke="var(--white)" stroke-width="1.6"/></svg>
        @vessolinhairstudio
      </li>
      <li>
        <svg viewBox="0 0 16 16" aria-hidden="true" fill="none" stroke="var(--white)" stroke-width="1.1"><circle cx="8" cy="8" r="6.8"/><ellipse cx="8" cy="8" rx="3" ry="6.8"/><path d="M1.2 8 H14.8 M2.3 4.5 H13.7 M2.3 11.5 H13.7"/></svg>
        www.vessolinhairstudio.example
      </li>
    </ul>

    <div class="front-brand">Vessolin<br>Hair<br>Studio</div>
  </section>

  <section class="card card-back" aria-label="Business card back">
    <div class="back-brand">Vessolin<br>Hair<br>Studio</div>

    <div class="services-heading">
      <p class="services-pill">OUR SERVICES</p>
    </div>
    <ul class="services-list">
      <li>Custom Haircuts</li>
      <li>Coloring</li>
      <li>Extensions</li>
      <li>And Barbering</li>
      <li>Beard Grooming</li>
    </ul>
  </section>
</body>
</html>
```